Trendy E Juice Product Labels Required

We are looking for design for an e Juice label line (the liquids used in electronic cigarettes). What we need is 5 product labels which eventually will be printed on 95mm x 40mm labels. Obviously the image will be created much larger than this but the aspect ratio should be scalable down to this size.

What each label must have is I would need is a background, a monster character, and space for a product name incorporated in to the design. The brand on this line is "Velvet Orbit". Whilst creatively, we are completely open to any concept, there is certain text which is necessary for incorporation in to each label. The attached file, "Example Label" shows these elements. NOTE: the attached file IS NOT a finished label.
Updates

Reason: Not received a design that we wish to proceed with.

Target Market(s)

25-35 year old vapers

Industry/Entity Type

Electronic

Requirements
Should not have
• Anything that may be construed as being targeted toward children.

```html
<!DOCTYPE html>
<html lang="en">
<head>
<meta charset="utf-8">
<title>Velvet Orbit – E-Liquid Label</title>
<link rel="stylesheet" href="https://fonts.googleapis.com/css2?family=Barlow+Semi+Condensed:ital,wght@0,400;0,500;0,600;1,400&display=swap">
<style>
  :root {
    --coral: #d9534b;
    --ink: #0c0c0c;
    --paper: #ffffff;
    --pattern-dark: #2a2a2a;
    --pattern-light: #8c8c8c;
  }
  html, body { margin: 0; padding: 0; overflow: hidden; background: var(--paper); }
  .label {
    position: relative;
    width: 1200px; height: 504px;
    background: var(--ink);
    color: var(--paper);
    font-family: "Barlow Semi Condensed", sans-serif;
    overflow: hidden;
  }
  .band { position: absolute; left: 0; width: 100%; background: var(--coral); z-index: 3; }
  .band--top { top: 0; height: 31px; }
  .band--bottom { top: 466px; height: 38px; }

  /* Left column */
  .legal { position: absolute; left: 9px; width: 330px; }
  .legal h2 { margin: 0; font-weight: 500; font-size: 27px; letter-spacing: 0.5px; line-height: 1; }
  .legal p { margin: 6px 0 0; font-size: 16px; line-height: 22.6px; letter-spacing: 0.2px; }
  .legal--warning { top: 38px; }
  .legal--ingredients { top: 332px; }

  /* Centre panel */
  .centre { position: absolute; left: 343px; top: 0; width: 471px; height: 504px; }
  .centre__pattern {
    position: absolute; inset: 0;
    background: linear-gradient(135deg, var(--pattern-dark), var(--pattern-light) 50%, var(--pattern-dark));
  }
  .centre__diamond { position: absolute; inset: 0; }
  .brand {
    position: absolute; left: 94px; top: 140px;
    color: var(--ink); font-weight: 600; line-height: 1;
  }
  .brand__line--one { display: block; font-size: 64px; letter-spacing: 2px; }
  .brand__line--two { display: block; font-size: 64px; letter-spacing: 2px; margin-top: 20px; }
  .brand__dot {
    position: absolute; left: 222px; top: -62px;
    width: 72px; height: 72px; border-radius: 50%; background: var(--coral);
  }
  .product-name {
    position: absolute; left: 94px; top: 331px; width: 271px; height: 43px;
    background: var(--coral); color: var(--paper);
    font-size: 30px; font-weight: 500; text-align: center; line-height: 43px;
  }
  .volume {
    position: absolute; left: 0; width: 100%; top: 416px;
    text-align: center; color: var(--ink); font-size: 21px;
  }

  /* Right column */
  .contact { position: absolute; left: 845px; top: 56px; width: 340px; }
  .contact__lead { margin: 0; font-style: italic; font-size: 17px; }
  .social { display: flex; gap: 34px; margin-top: 14px; padding: 0; list-style: none; }
  .social__item {
    width: 62px; height: 62px; border-radius: 50%; background: var(--coral);
    display: flex; align-items: center; justify-content: center;
    font-size: 13px; font-weight: 500; color: var(--paper);
  }
  .contact__web { margin: 16px 0 0; font-weight: 600; font-size: 17px; line-height: 25px; }
  .distributor { position: absolute; left: 845px; top: 265px; font-size: 16px; line-height: 22px; margin: 0; }
  .notices { position: absolute; left: 850px; top: 382px; }
</style>
</head>
<body>
<main class="label">
  <div class="band band--top"></div>
  <div class="band band--bottom"></div>

  <section class="legal legal--warning">
    <h2>WARNING</h2>
    <p>This product contains nicotine, a substance which is known to cause birth defects. Do not swallow. Avoid contact with skin. Keep out of reach of children and pets. This product is intended for use by persons 18 and older. Pregnant women and those breast feeding should not use this product. May contain traces of nuts.</p>
  </section>

  <section class="legal legal--ingredients">
    <h2>INGREDIENTS</h2>
    <p>USP/EP Propelyn Glycol (XX%), USP/EP Vetetable Glycerin (XX%), USP/EP Nicotine, Natural and Artificial Flavorings.</p>
  </section>

  <section class="centre">
    <div class="centre__pattern" role="img" aria-label="Black and white geometric lattice pattern background"></div>
    <svg class="centre__diamond" width="471" height="504" viewBox="0 0 471 504" aria-hidden="true">
      <polygon points="236,10 460,254 236,498 12,254" fill="#ffffff"/>
    </svg>
    <div class="brand">
      <span class="brand__dot"></span>
      <span class="brand__line--one">VELVET</span>
      <span class="brand__line--two">ORBIT</span>
    </div>
    <div class="product-name">Product Name</div>
    <div class="volume">30ml</div>
  </section>

  <section class="contact">
    <p class="contact__lead">Find us at:</p>
    <ul class="social">
      <li class="social__item">Snapgrid</li>
      <li class="social__item">Friendly</li>
      <li class="social__item">Chirper</li>
    </ul>
    <p class="contact__web">www.velvetorbit.com<br>@velvetorbit</p>
  </section>

  <p class="distributor">Distributed by:<br>Velvet Orbit<br>Address<br>Telephone</p>

  <svg class="notices" width="300" height="70" viewBox="0 0 300 70" aria-label="Safety notices">
    <g fill="none" stroke="#fff" stroke-width="6" stroke-linecap="round">
      <path d="M20 46 A20 20 0 0 1 18 18"/>
      <path d="M30 12 A20 20 0 0 1 54 28"/>
      <path d="M52 44 A20 20 0 0 1 30 56"/>
    </g>
    <g fill="#fff">
      <polygon points="16,14 24,22 12,24"/>
      <polygon points="56,22 58,34 48,30"/>
      <polygon points="30,50 24,58 34,62"/>
      <polygon points="107,6 140,62 74,62"/>
    </g>
    <rect x="104" y="24" width="6" height="22" fill="#0c0c0c"/>
    <rect x="104" y="50" width="6" height="6" fill="#0c0c0c"/>
    <g fill="#fff">
      <circle cx="168" cy="14" r="6"/>
      <rect x="176" y="24" width="26" height="34" rx="2"/>
      <rect x="172" y="18" width="34" height="4"/>
    </g>
    <g fill="none" stroke="#fff" stroke-width="5">
      <circle cx="261" cy="33" r="27"/>
      <line x1="242" y1="14" x2="280" y2="52"/>
    </g>
    <text x="261" y="42" fill="#fff" font-family="Barlow Semi Condensed, sans-serif" font-weight="600" font-size="26" text-anchor="middle">18</text>
  </svg>
</main>
</body>
</html>
```